Working Capital graphics

Our business advisory firm requires 9 images to be re-created and improved in the branding of our business.

The 9 images have been uploaded below and the colours and branding of the business can be found at the website www.tallowmereadvisory.com.au

```html
<!DOCTYPE html>
<html lang="en">
<head>
<meta charset="utf-8">
<title>Working Capital Levers Along the Value Chain</title>
<link rel="stylesheet" href="https://fonts.googleapis.com/css2?family=Figtree:ital,wght@0,400;1,700;1,800&display=swap">
<style>
  :root {
    --inventory: #56a8dc;
    --payables: #f09d41;
    --receivables: #3957a6;
    --stage-text: #111111;
    --lever-text: #ffffff;
    --connector: #000000;
    --legend-text: #1a1a1a;
    --background: #ffffff;
  }
  html, body {
    margin: 0;
    padding: 0;
    overflow: hidden;
    background: var(--background);
  }
  .canvas {
    position: relative;
    width: 1200px;
    height: 1000px;
    overflow: hidden;
    font-family: "Figtree", "Helvetica Neue", Arial, sans-serif;
  }
  .chain-graphic {
    position: absolute;
    inset: 0;
  }
  .stage-shape { fill: var(--inventory); }
  .connector { stroke: var(--connector); stroke-width: 1.6; fill: none; }

  .stage-label {
    position: absolute;
    top: 505px;
    height: 117px;
    display: flex;
    align-items: center;
    justify-content: center;
    text-align: center;
    font-style: italic;
    font-weight: 800;
    font-size: 17px;
    line-height: 18px;
    color: var(--stage-text);
  }
  .stage-label--left { justify-content: flex-start; text-align: left; }
  .stage-label--tight { font-size: 15px; letter-spacing: -0.3px; }

  .lever {
    position: absolute;
    height: 97px;
    display: flex;
    align-items: center;
    justify-content: center;
    text-align: center;
    font-style: italic;
    font-weight: 700;
    font-size: 17px;
    line-height: 23px;
    color: var(--lever-text);
    box-sizing: border-box;
    padding: 0 4px;
  }
  .lever--payables { background: var(--payables); }
  .lever--receivables { background: var(--receivables); }

  .legend {
    position: absolute;
    top: 813px;
    font-size: 17px;
    line-height: 25px;
    color: var(--legend-text);
    display: flex;
    align-items: flex-start;
    gap: 10px;
  }
  .legend-swatch {
    width: 26px;
    height: 26px;
    flex: none;
  }
  .legend-swatch--inventory { background: var(--inventory); }
  .legend-swatch--payables { background: var(--payables); }
  .legend-swatch--receivables { background: var(--receivables); }
</style>
</head>
<body>
<main class="canvas">
  <svg class="chain-graphic" width="1200" height="1000" viewBox="0 0 1200 1000" aria-hidden="true">
    <g class="value-chain">
      <polygon class="stage-shape" points="47,505 160,505 183,563 160,622 47,622"/>
      <polygon class="stage-shape" points="167,505 280,505 302,563 280,622 167,622 189,563"/>
      <polygon class="stage-shape" points="287,505 400,505 421,563 400,622 287,622 309,563"/>
      <polygon class="stage-shape" points="406,505 519,505 541,563 519,622 406,622 428,563"/>
      <polygon class="stage-shape" points="526,505 638,505 660,563 638,622 526,622 548,563"/>
      <polygon class="stage-shape" points="645,505 758,505 780,563 758,622 645,622 667,563"/>
      <polygon class="stage-shape" points="764,505 877,505 899,563 877,622 764,622 786,563"/>
      <polygon class="stage-shape" points="884,505 985,505 1007,563 985,622 884,622 906,563"/>
      <polygon class="stage-shape" points="1009,505 1127,505 1150,563 1127,622 1009,622 1031,563"/>
    </g>
    <g class="connectors">
      <line class="connector" x1="127" y1="451" x2="127" y2="505"/>
      <line class="connector" x1="348" y1="334" x2="348" y2="354"/>
      <line class="connector" x1="348" y1="451" x2="348" y2="505"/>
      <polyline class="connector" points="510,451 510,472 231,472 231,505"/>
      <line class="connector" x1="467" y1="472" x2="467" y2="505"/>
      <line class="connector" x1="755" y1="451" x2="755" y2="505"/>
      <line class="connector" x1="931" y1="334" x2="931" y2="354"/>
      <line class="connector" x1="931" y1="451" x2="931" y2="505"/>
      <line class="connector" x1="1068" y1="451" x2="1068" y2="505"/>

      <line class="connector" x1="348" y1="622" x2="348" y2="667"/>
      <polyline class="connector" points="366,622 366,645 812,645 812,622"/>
      <line class="connector" x1="467" y1="622" x2="467" y2="645"/>
      <line class="connector" x1="699" y1="622" x2="699" y2="645"/>
      <line class="connector" x1="580" y1="622" x2="580" y2="678"/>
      <line class="connector" x1="931" y1="622" x2="931" y2="667"/>
      <line class="connector" x1="1068" y1="622" x2="1068" y2="667"/>
    </g>
  </svg>

  <div class="stage-label" style="left:47px;width:126px;">Design</div>
  <div class="stage-label stage-label--left" style="left:199px;width:90px;">Order/<br>material<br>planning</div>
  <div class="stage-label" style="left:309px;width:106px;">Purchasing</div>
  <div class="stage-label stage-label--tight" style="left:426px;width:112px;">Manufacturing</div>
  <div class="stage-label" style="left:546px;width:112px;">Pre-assembly</div>
  <div class="stage-label" style="left:667px;width:106px;">Assembly</div>
  <div class="stage-label stage-label--left" style="left:797px;width:100px;">Packaging/<br>shipping</div>
  <div class="stage-label" style="left:906px;width:92px;">Sales</div>
  <div class="stage-label stage-label--left" style="left:1040px;width:110px;">After sales/<br>service</div>

  <div class="lever lever--payables" style="left:47px;top:354px;width:161px;">Reduce part<br>variants/<br>releases</div>
  <div class="lever lever--receivables" style="left:281px;top:238px;width:135px;">Modify<br>payment<br>conditions</div>
  <div class="lever lever--receivables" style="left:281px;top:354px;width:135px;">Optimize<br>payment<br>processes</div>
  <div class="lever lever--payables" style="left:430px;top:354px;width:160px;">Rethink delivery<br>schedules and<br>warehousing</div>
  <div class="lever lever--payables" style="left:675px;top:354px;width:160px;">Optimize<br>product<br>testing</div>
  <div class="lever lever--receivables" style="left:865px;top:238px;width:131px;">Improve<br>payment/<br>schemes</div>
  <div class="lever lever--receivables" style="left:865px;top:354px;width:131px;">Reduce/<br>overdue<br>receivables</div>
  <div class="lever lever--receivables" style="left:1009px;top:354px;width:131px;">Establish new<br>payment<br>conditions</div>

  <div class="lever lever--payables" style="left:281px;top:667px;width:135px;">Optimize<br>external<br>purchasing</div>
  <div class="lever lever--payables" style="left:865px;top:667px;width:131px;">Reduce<br>inventory</div>
  <div class="lever lever--payables" style="left:1009px;top:667px;width:131px;">Reduce<br>inventory</div>

  <div class="legend" style="left:550px;">
    <span class="legend-swatch legend-swatch--inventory"></span>
    <span>Inventory</span>
  </div>
  <div class="legend" style="left:688px;">
    <span class="legend-swatch legend-swatch--payables"></span>
    <span>Payables and<br>prepayments made</span>
  </div>
  <div class="legend" style="left:906px;">
    <span class="legend-swatch legend-swatch--receivables"></span>
    <span>Receivables and<br>prepayments received</span>
  </div>
</main>
</body>
</html>
```